Business Card for a Jewellery Brand

Business card for an upscale jewellery brand. Attached is the brand logo and icon and color board. I am looking for two card versions: one for the founder and one is generic. The card should be elegant and convey upscale and premium feel. I am open to both square and rectangle card shapes.

Industry/Entity Type

Jewelry

Contact Information for Business Card

Two cards: (1) Sunela Parvaniya (Founder) (2) General
(1) Sunela Parvaniya card should have Name: Sunela Parvaniya, Title: Founder Email id: sunela@quiremo.com.au. Phone no: +61452913307
(2) Generic card should have Email id: info@quiremo.com.au. Phone no: +61436207518

Requirements
Must have
• Workmark
• ICON
• Phone no
• Email ID
• ABN: 58219740312 (Note: ABN is Business number in Australia)
• Website: www.quiremo.com.au
• Instagram: quiremo_jewellery
• Facebook: @quiremojewellery
Nice to have
• Tagline

```html
<!DOCTYPE html>
<html lang="en">
<head>
<meta charset="utf-8">
<title>Quiremo – Business Card</title>
<link rel="stylesheet" href="https://fonts.googleapis.com/css2?family=Montserrat:wght@400;500;700&family=Open+Sans:wght@400;600&display=swap">
<style>
  :root {
    --blush: #e59693;
    --blush-deep: #e38a88;
    --paper: #ffffff;
    --ink: #2f2f2f;
    --swoosh: #e6e6e8;
    --backdrop: #efeae6;
  }
  * { box-sizing: border-box; margin: 0; padding: 0; }
  html, body {
    width: 1200px; height: 900px; overflow: hidden;
    background: var(--backdrop);
  }
  .stage {
    position: relative; width: 1200px; height: 900px;
    display: flex; align-items: center; justify-content: center; gap: 40px;
  }
  .card {
    position: relative; width: 540px; height: 309px; overflow: hidden;
    box-shadow: 0 6px 18px rgba(0,0,0,.12);
  }

  /* Front face */
  .card--front {
    background: var(--blush);
    display: flex; align-items: center; justify-content: center;
  }
  .brand-mark {
    font-family: "Montserrat", sans-serif; font-weight: 500;
    font-size: 40px; letter-spacing: 12px; color: var(--paper);
  }

  /* Back face */
  .card--back { background: var(--paper); }
  .card__wave { position: absolute; inset: 0; width: 100%; height: 100%; }
  .holder { position: absolute; left: 46px; top: 72px; }
  .holder__name {
    font-family: "Montserrat", sans-serif; font-weight: 700;
    font-size: 17px; color: var(--blush-deep); text-transform: uppercase;
    letter-spacing: .3px;
  }
  .holder__title {
    font-family: "Open Sans", sans-serif; font-size: 13px; color: var(--ink);
    margin: 2px 0 0 8px;
  }
  .contacts {
    position: absolute; left: 74px; top: 140px; list-style: none;
    font-family: "Open Sans", sans-serif; font-size: 13.5px; color: var(--ink);
  }
  .contacts li { display: flex; align-items: center; gap: 8px; height: 20px; }
  .contacts svg { width: 11px; height: 11px; flex: none; fill: var(--blush-deep); }
  .socials {
    position: absolute; left: 72px; top: 210px; list-style: none;
    font-family: "Open Sans", sans-serif; font-size: 14px; color: var(--ink);
  }
  .socials li { display: flex; align-items: center; gap: 8px; height: 25px; }
  .socials__dot {
    width: 18px; height: 18px; border-radius: 50%; background: var(--blush-deep);
  }
  .card__brand {
    position: absolute; right: 34px; top: 92px;
    font-family: "Montserrat", sans-serif; font-weight: 500;
    font-size: 28px; letter-spacing: 9px; color: var(--blush);
  }
  .abn {
    position: absolute; right: 26px; top: 230px;
    font-family: "Open Sans", sans-serif; font-size: 11px; color: var(--paper);
  }
</style>
</head>
<body>
<main class="stage">

  <section class="card card--front" aria-label="Business card front">
    <span class="brand-mark">QUIREMO</span>
  </section>

  <section class="card card--back" aria-label="Business card back">
    <svg class="card__wave" viewBox="0 0 540 309" preserveAspectRatio="none" aria-hidden="true">
      <path d="M0,268 C170,300 360,262 540,128 L540,146 C360,282 170,306 0,290 Z" fill="var(--swoosh)"/>
      <path d="M0,292 C170,306 360,284 540,150 L540,309 L0,309 Z" fill="var(--blush)"/>
    </svg>

    <div class="holder">
      <h1 class="holder__name">Sunela Parvaniya</h1>
      <p class="holder__title">Founder</p>
    </div>

    <ul class="contacts">
      <li>
        <svg viewBox="0 0 24 24"><path d="M6.6 10.8a15 15 0 0 0 6.6 6.6l2.2-2.2a1 1 0 0 1 1-.25 11.4 11.4 0 0 0 3.6.57 1 1 0 0 1 1 1V20a1 1 0 0 1-1 1A17 17 0 0 1 3 4a1 1 0 0 1 1-1h3.5a1 1 0 0 1 1 1c0 1.25.2 2.45.57 3.57a1 1 0 0 1-.25 1z"/></svg>
        +61452913307
      </li>
      <li>
        <svg viewBox="0 0 24 24"><path d="M2 5h20v14H2z M2 5l10 8 10-8" stroke="#fff" stroke-width="1.5"/></svg>
        sunela@quiremo.com.au
      </li>
      <li>
        <svg viewBox="0 0 24 24"><circle cx="12" cy="12" r="10"/></svg>
        www.quiremo.com.au
      </li>
    </ul>

    <ul class="socials">
      <li><span class="socials__dot"></span>@quiremojewellery</li>
      <li><span class="socials__dot"></span>quiremo_jewellery</li>
    </ul>

    <span class="card__brand">QUIREMO</span>
    <span class="abn">ABN: 58219740312</span>
  </section>

</main>
</body>
</html>
```